Business Card design which attached logo. Company is called Crestline Shield and main colours are Orange & Black.

Company specialises in Paint Protection and Detailing for supercars.

Details needed on business card:

Sales

Address: Unit 14, 517 Hadley Road, Fernvale Heights, NSW 2591

Phone: 02 6194 2738

website: www.crestlineshield.com.au

Email: sales@crestlineshield.com.au

```html
<!DOCTYPE html>
<html lang="en">
<head>
<meta charset="utf-8">
<title>Crestline Shield – Business Card</title>
<link href="https://fonts.googleapis.com/css2?family=Montserrat:wght@300;400&display=swap" rel="stylesheet">
<style>
  :root {
    --stage: #2b2c30;
    --card-black: #0b0c0e;
    --card-white: #ffffff;
    --orange: #f0582a;
    --grey-text: #5e5e62;
  }
  * { margin: 0; padding: 0; box-sizing: border-box; }
  html, body {
    width: 1200px; height: 900px; overflow: hidden;
    background: var(--stage);
    font-family: "Montserrat", Arial, sans-serif;
  }
  .card {
    position: absolute;
    left: 290px;
    width: 620px; height: 354px;
    background: var(--card-black);
    overflow: hidden;
    box-shadow: 0 10px 30px rgba(0,0,0,.45);
  }
  .card--front { top: 72px; }
  .card--back { top: 474px; }

  .swoosh { position: absolute; inset: 0; width: 100%; height: 100%; }

  .brand {
    position: absolute;
    display: flex; align-items: center; gap: 10px;
    color: var(--orange);
    font-weight: 300;
    text-transform: uppercase;
    letter-spacing: .06em;
    white-space: nowrap;
  }
  .brand__dot {
    border-radius: 50%;
    background: var(--orange);
    flex: none;
  }
  .card--front .brand { left: 40px; top: 44px; font-size: 21px; }
  .card--front .brand__dot { width: 10px; height: 10px; }

  .person-name {
    position: absolute;
    right: 44px; top: 118px;
    color: var(--orange);
    font-weight: 300;
    font-size: 30px;
    letter-spacing: .06em;
    text-transform: uppercase;
    white-space: nowrap;
  }

  .contact {
    position: absolute;
    right: 22px; top: 238px;
    list-style: none;
    text-align: right;
    font-size: 13px;
    line-height: 20px;
    white-space: nowrap;
  }
  .contact li { display: flex; justify-content: flex-end; align-items: center; gap: 10px; }
  .contact__address { color: var(--orange); padding-right: 24px; }
  .contact__line { color: var(--grey-text); }
  .contact__icon { width: 14px; height: 14px; flex: none; }

  .card--back .brand {
    left: 50%; top: 50%;
    transform: translate(-50%, -50%);
    font-size: 36px;
    gap: 14px;
  }
  .card--back .brand__dot { width: 14px; height: 14px; }
</style>
</head>
<body>

<section class="card card--front" aria-label="Business card front">
  <svg class="swoosh" viewBox="0 0 620 354" preserveAspectRatio="none" aria-hidden="true">
    <path d="M0,92 C120,70 230,140 340,178 C430,208 520,214 620,212 L620,228 C520,232 430,226 340,198 C230,162 120,100 0,112 Z" fill="var(--orange)"/>
    <path d="M0,112 C120,100 230,162 340,198 C430,226 520,232 620,228 L620,354 L0,354 Z" fill="var(--card-white)"/>
    <path d="M0,118 C90,112 170,150 250,196 C180,168 90,140 0,146 Z" fill="var(--orange)"/>
    <path d="M0,150 C70,148 130,170 190,200 C130,184 70,172 0,176 Z" fill="var(--card-black)"/>
  </svg>

  <div class="brand"><span class="brand__dot"></span>Crestline Shield</div>

  <p class="person-name">Liam Carter</p>

  <ul class="contact">
    <li class="contact__address">Unit 14, 517 Hadley Road</li>
    <li class="contact__address">Fernvale Heights, NSW 2591</li>
    <li class="contact__line">02 6194 2738
      <svg class="contact__icon" viewBox="0 0 16 16" aria-hidden="true"><path d="M4 1.5 6 5 4.6 6.6c.8 1.8 2.2 3.2 4.8 4.8L11 10l3.5 2-1 2.5C7.5 14 2 8.5 1.5 2.5Z" fill="var(--orange)"/></svg>
    </li>
    <li class="contact__line">sales@crestlineshield.com.au
      <svg class="contact__icon" viewBox="0 0 16 16" aria-hidden="true"><rect x="1" y="3" width="14" height="10" fill="var(--orange)"/><path d="M1.5 3.5 8 9l6.5-5.5" fill="none" stroke="#fff" stroke-width="1.2"/></svg>
    </li>
    <li class="contact__line">www.crestlineshield.com.au
      <svg class="contact__icon" viewBox="0 0 16 16" aria-hidden="true"><circle cx="8" cy="8" r="7" fill="var(--orange)"/><path d="M1 8h14M8 1c-3 3-3 11 0 14M8 1c3 3 3 11 0 14M2.5 4.5h11M2.5 11.5h11" fill="none" stroke="#fff" stroke-width=".9"/></svg>
    </li>
  </ul>
</section>

<section class="card card--back" aria-label="Business card back">
  <div class="brand"><span class="brand__dot"></span>Crestline Shield</div>
</section>

</body>
</html>
```